Brightmill Data Works

Our company is about IT hardwares and IT solutions. IT hardware such as PC, RAMS, storage and servers. IT solutions such as project management, BA. We are also selling new technology too.

Target Market(s)

Consumer, Small to Medium Business, Corporate

Requirements
Must have
• The business card must have the following:
• Name:
• Title:
• Contact Number:
• Email address:
• Website:
• Color: Must match the logo color upgrade

```html
<!DOCTYPE html>
<html lang="en">
<head>
<meta charset="utf-8">
<title>Brightmill Data Works – Business Card</title>
<link rel="stylesheet" href="https://fonts.googleapis.com/css2?family=Saira:wght@700;800&family=Arimo:wght@400;700&display=swap">
<style>
  :root {
    --backdrop: #3a3a3a;
    --card: #1f1f20;
    --card-edge: #2a2a2b;
    --orange: #e4892c;
    --orange-deep: #d06a22;
    --white: #f4f4f4;
    --text-soft: #e6e6e6;
  }
  * { box-sizing: border-box; margin: 0; padding: 0; }
  html, body {
    width: 1200px; height: 1189px; overflow: hidden;
    background: var(--backdrop);
  }
  .sheet {
    width: 1200px; height: 1189px;
    display: flex; flex-direction: column; align-items: center; justify-content: center;
    gap: 40px;
  }
  .card {
    position: relative;
    width: 945px; height: 540px;
    background: var(--card);
    border: 1px solid var(--card-edge);
    border-radius: 34px;
    overflow: hidden;
    box-shadow: 0 18px 40px rgba(0,0,0,.45);
  }

  /* Front face */
  .card--front {
    display: flex; align-items: center; justify-content: center;
  }
  .brand {
    display: flex; flex-direction: column; align-items: center; gap: 22px;
  }
  .brand__dot {
    width: 46px; height: 46px; border-radius: 50%;
    background: var(--orange);
  }
  .brand__name {
    font-family: "Saira", sans-serif;
    font-weight: 800;
    font-size: 64px;
    letter-spacing: 2px;
    line-height: 1;
    color: var(--white);
    text-transform: uppercase;
    text-align: center;
  }

  /* Back face */
  .card--back .wordmark {
    position: absolute; left: 62px; top: 92px;
    font-family: "Saira", sans-serif;
    font-weight: 800;
    font-size: 46px;
    letter-spacing: 1.5px;
    line-height: 1.02;
    color: var(--white);
    text-transform: uppercase;
  }
  .card--back .edge-tab {
    position: absolute; left: -26px; top: 272px;
    width: 52px; height: 52px; border-radius: 50%;
    background: var(--orange);
  }
  .person {
    position: absolute; left: 92px; top: 258px;
    font-family: "Arimo", sans-serif;
  }
  .person__name {
    font-weight: 700; font-size: 26px; letter-spacing: .5px;
    color: var(--white); text-transform: uppercase;
  }
  .person__title {
    font-size: 23px; color: var(--orange); margin-top: 2px;
  }
  .address {
    position: absolute; left: 92px; top: 352px;
    font-family: "Arimo", sans-serif;
    font-size: 23px; line-height: 1.25;
    color: var(--text-soft);
  }
  .contacts {
    position: absolute; left: 92px; top: 418px;
    list-style: none;
    font-family: "Arimo", sans-serif;
    font-size: 23px; line-height: 1.25;
    color: var(--text-soft);
  }
  .contacts li { display: flex; align-items: center; gap: 12px; }
  .contacts svg { width: 20px; height: 20px; flex: none; }

  .mark-name {
    position: absolute; right: 70px; top: 150px;
    display: flex; flex-direction: column; align-items: flex-start; gap: 18px;
  }
  .mark-name__dot {
    width: 56px; height: 56px; border-radius: 50%;
    background: var(--orange);
  }
  .mark-name__text {
    font-family: "Saira", sans-serif;
    font-weight: 800;
    font-size: 64px;
    line-height: .98;
    letter-spacing: 1px;
    color: var(--orange);
    text-transform: uppercase;
  }
</style>
</head>
<body>
<main class="sheet">

  <section class="card card--front" aria-label="Card front">
    <div class="brand">
      <span class="brand__dot"></span>
      <h1 class="brand__name">Brightmill<br>Data Works</h1>
    </div>
  </section>

  <section class="card card--back" aria-label="Card back">
    <h2 class="wordmark">Brightmill<br>Data Works</h2>
    <span class="edge-tab"></span>

    <div class="person">
      <p class="person__name">Mara Ellison</p>
      <p class="person__title">Manager</p>
    </div>

    <p class="address">PO BOX 418 Harbour Lane<br>7th street Alderport</p>

    <ul class="contacts">
      <li>
        <svg viewBox="0 0 20 20" aria-hidden="true"><path fill="var(--orange)" d="M2 7c0-2 3-4 8-4s8 2 8 4v2h-4V7.5c-1-.6-2.4-.9-4-.9s-3 .3-4 .9V9H2zM5 10l2-2h6l2 2 1 7H4z"/><circle cx="10" cy="13" r="2" fill="var(--card)"/></svg>
        555-014-2290
      </li>
      <li>
        <svg viewBox="0 0 20 20" aria-hidden="true"><rect x="1.5" y="4" width="17" height="12" rx="1" fill="var(--orange)"/><path d="M2 5l8 6 8-6" fill="none" stroke="var(--card)" stroke-width="1.4"/></svg>
        hello@brightmillmail.com
      </li>
      <li>
        <svg viewBox="0 0 20 20" aria-hidden="true"><circle cx="10" cy="10" r="8.5" fill="var(--orange)"/><g fill="none" stroke="var(--card)" stroke-width="1.1"><ellipse cx="10" cy="10" rx="3.6" ry="8.5"/><path d="M1.5 10h17M3 6h14M3 14h14"/></g></svg>
        www.brightmillworks.com
      </li>
    </ul>

    <div class="mark-name">
      <span class="mark-name__dot"></span>
      <p class="mark-name__text">Brightmill<br>Data<br>Works</p>
    </div>
  </section>

</main>
</body>
</html>
```